Logistics Website Design

See website https://tqfreightglobal.com for theme and color details. Need the site to be re-done and reflect some of the designs shown in this list here: https://pixelvane.com/tags/logistics-company-website

Target Market(s)

Logistics & Transportation

Industry/Entity Type

Logistics and Supply Chain

Coding

Number of Pages Required

5+ page

Requirements
Must have
• Colors must match theme of logo. Looking for a sleek, interactive design.

```html
<!DOCTYPE html>
<html lang="en">
<head>
<meta charset="utf-8">
<title>TQ Freight Global — Logistics</title>
<link rel="stylesheet" href="https://fonts.googleapis.com/css2?family=Bebas+Neue&family=Michroma&family=Poppins:wght@400;500;600&display=swap">
<style>
:root{
  --orange:#f26b3a;
  --orange-deep:#d9542a;
  --salmon:#ec8a68;
  --cream:#fdf1ec;
  --ink:#1a0a05;
  --brown:#2a120a;
  --brown-2:#3d1b0f;
  --line:#6b3a27;
  --white:#ffffff;
  --muted:#d9c3b9;
}
*{box-sizing:border-box;margin:0;padding:0}
html,body{width:1200px;height:4975px;overflow:hidden}
body{position:relative;background:var(--ink);font-family:"Poppins",sans-serif;color:var(--white)}
.abs{position:absolute}
.display{font-family:"Bebas Neue",sans-serif;font-weight:400;letter-spacing:.5px;line-height:1}
.eyebrow{font-family:"Michroma",sans-serif;font-size:11px;letter-spacing:2px;text-transform:uppercase;color:var(--orange)}
.btn{position:absolute;display:flex;align-items:center;gap:10px;background:var(--orange);color:#fff;border-radius:30px;font-family:"Bebas Neue",sans-serif;font-size:17px;letter-spacing:.5px;padding:0 8px 0 26px;height:40px}
.btn .arrow{width:28px;height:28px;border-radius:50%;background:var(--ink);display:flex;align-items:center;justify-content:center;margin-left:auto}
.ph{position:absolute}

/* hero */
.hero{top:0;left:0;width:1200px;height:715px;clip-path:polygon(0 0,100% 0,100% 580px,50% 715px,0 580px);background:linear-gradient(100deg,#1f0c06 0%,#3b1a0e 35%,#6b4230 60%,#9a7a6c 100%)}
.hero-photo{left:560px;top:60px;width:640px;height:520px;background:radial-gradient(ellipse at 55% 45%,#e9e4e6 0%,#a99088 35%,rgba(80,45,30,.4) 65%,transparent 80%)}
.nav{top:22px;left:0;width:1200px;height:40px}
.brand-badge{left:95px;top:4px;width:150px;height:136px;border-radius:50%;border:3px solid var(--orange);background:var(--brown);display:flex;align-items:center;justify-content:center;text-align:center;font-family:"Bebas Neue",sans-serif;font-size:22px;line-height:1;color:var(--white)}
.nav-links{left:295px;top:34px;display:flex;gap:44px;font-family:"Bebas Neue",sans-serif;font-size:15px;letter-spacing:.5px}
.nav-links span.on{color:var(--orange)}
.hero h1{left:98px;top:208px;font-size:66px}
.hero h1 .boxed{background:var(--white);color:var(--ink);padding:0 6px;border-radius:4px}
.hero-copy{left:104px;top:358px;width:500px;border-left:2px solid var(--orange);padding-left:14px;font-size:14.5px;line-height:1.55;color:var(--muted)}

/* stats */
.stat{top:735px;width:200px;text-align:center}
.stat b{display:block;font-family:"Bebas Neue",sans-serif;font-weight:400;font-size:58px;line-height:1}
.stat small{font-family:"Bebas Neue",sans-serif;font-size:15px;color:var(--orange);letter-spacing:.5px}
.stat-div{top:738px;width:1px;height:80px;background:var(--line)}
.about-bg{top:850px;left:0;width:1200px;height:638px;clip-path:polygon(50% 0,100% 155px,100% 100%,0 100%,0 155px);background:linear-gradient(180deg,#5a2c18 0%,#2e140a 35%,#1e0c06 100%)}

/* about */
.about-photo{left:112px;top:1018px;width:452px;height:362px;border-radius:6px;background:linear-gradient(135deg,#52627a 0%,#9aa0a6 40%,#e0d6cf 60%,#8c6a55 100%)}
.play{left:526px;top:1162px;width:72px;height:72px;border-radius:50%;background:var(--ink);border:3px solid var(--ink);display:flex;align-items:center;justify-content:center}
.about h2{left:636px;top:1040px;font-size:58px;line-height:1.02}
.about p{left:636px;top:1182px;width:496px;font-size:16px;line-height:1.55;color:var(--muted)}

/* services */
.services{top:1488px;left:0;width:1200px;height:614px;background:linear-gradient(90deg,#fff 0%,#fbe2d7 40%,var(--salmon) 100%);color:var(--ink)}
.sec-head{width:1200px;text-align:center}
.sec-head .eyebrow{color:var(--ink);font-size:10px}
.card{position:absolute;top:168px;width:255px;height:342px;border-radius:6px;background:linear-gradient(180deg,#3a1509,#220b05);color:#fff;overflow:hidden;padding:38px 36px 0}
.card.active{background:linear-gradient(180deg,var(--orange),#e2582b)}
.card h3{font-family:"Bebas Neue",sans-serif;font-weight:400;font-size:26px;line-height:1;color:var(--orange)}
.card.active h3{color:#fff}
.card p{font-size:11px;line-height:1.55;margin-top:12px;color:#e8d5cc}
.card .img{position:absolute;left:0;bottom:0;width:100%;height:150px}
.mini-btn{display:inline-flex;align-items:center;gap:8px;margin-top:12px;background:var(--ink);border-radius:20px;padding:4px 5px 4px 14px;font-family:"Bebas Neue",sans-serif;font-size:12px}
.mini-btn i{width:18px;height:18px;border-radius:50%;background:var(--orange);display:inline-block}

/* why */
.why{top:2102px;left:0;width:1200px;height:674px;background:radial-gradient(ellipse at 50% 55%,#3a1a0e 0%,#1e0c06 60%)}
.feat h4{font-family:"Bebas Neue",sans-serif;font-weight:400;font-size:25px;line-height:1.05}
.feat p{font-size:11.5px;line-height:1.6;color:var(--muted);margin-top:10px}
.icon-ring{position:absolute;width:94px;height:94px;border-radius:50%;border:3px solid var(--orange);background:var(--brown);display:flex;align-items:center;justify-content:center}
.center-badge{left:455px;top:218px;width:288px;height:288px;border-radius:50%;background:radial-gradient(circle,#3f1c10,#1e0c06);border:4px solid var(--orange);display:flex;align-items:center;justify-content:center;text-align:center;font-family:"Bebas Neue",sans-serif;font-size:40px;line-height:1;color:#fff}

/* industries */
.industries{top:2776px;left:0;width:1200px;height:527px;background:linear-gradient(90deg,#fff 0%,#fbe2d7 40%,var(--salmon) 100%);color:var(--ink)}
.ind{position:absolute;top:224px;width:193px;height:170px;background:var(--ink);border-radius:4px;color:#fff;text-align:center;font-family:"Bebas Neue",sans-serif;font-size:17px;padding-top:30px}
.ind.active{top:211px;height:206px;background:linear-gradient(180deg,#3a1509,#1a0a05);padding-top:43px}
.ind .tile{width:56px;height:56px;margin:0 auto 30px;background:var(--orange);border-radius:4px;display:flex;align-items:center;justify-content:center}

/* testimonials */
.testi h2{left:112px;top:3477px;font-size:58px;line-height:1.02}
.quote{position:absolute;top:3412px;width:323px;height:305px;border:1px solid var(--line);border-radius:6px;padding:30px 40px}
.quote .qm{font-family:"Bebas Neue",sans-serif;font-size:90px;line-height:.6;color:#5a3022}
.quote p{font-size:12px;line-height:1.9;color:var(--muted);margin-top:16px}
.who{display:flex;align-items:center;gap:12px;margin-top:12px}
.who .av{width:36px;height:36px;border-radius:50%;background:#7c8b7e}
.who b{font-family:"Bebas Neue",sans-serif;font-weight:400;font-size:17px}
.who .stars{color:var(--orange);font-size:13px;letter-spacing:2px}
.circ-btn{position:absolute;top:3720px;width:30px;height:30px;border-radius:50%;border:1px solid var(--orange);display:flex;align-items:center;justify-content:center}

/* contact */
.contact{top:3825px;left:0;width:1200px;height:619px;background:linear-gradient(180deg,#1e0c06 0%,#2a120a 55%,#7a3f28 100%)}
.field{position:absolute;height:48px;border:1px solid #8a5a47;border-radius:3px;display:flex;align-items:center;gap:10px;padding-left:20px;font-size:12px;color:#fff}

/* footer */
.footer{top:4444px;left:0;width:1200px;height:531px;background:var(--ink)}
.foot-link{position:absolute;left:377px;width:210px;height:52px;border-bottom:1px solid #3d2218;display:flex;align-items:center;gap:22px;padding-left:0;font-family:"Bebas Neue",sans-serif;font-size:22px}
.foot-col h5{font-family:"Bebas Neue",sans-serif;font-weight:400;font-size:22px}
.foot-col li{list-style:none;font-family:"Bebas Neue",sans-serif;font-size:20px;color:#d9c3b9;margin-top:14px}
.foot-col li::before{content:"»";color:var(--orange);margin-right:10px}
.big-word{left:0;top:4815px;width:1200px;text-align:center;font-family:"Bebas Neue",sans-serif;font-size:128px;color:#2a1610;letter-spacing:6px}
</style>
</head>
<body>

<!-- HERO -->
<section class="abs hero">
  <div class="ph hero-photo" role="img" aria-label="Photo of a white semi-truck driving on a highway at dusk"></div>
</section>
<header class="abs nav">
  <div class="abs brand-badge">TQ Freight<br>Global</div>
  <nav class="abs nav-links" style="top:12px">
    <span class="on">Home</span><span>Services</span><span>Industries</span><span>About Us</span><span>Contact Us</span>
  </nav>
  <div class="btn" style="left:940px;top:2px;width:175px;height:38px;font-size:15px;padding-left:28px">Request a Quote <span class="arrow"><svg width="12" height="12" viewBox="0 0 12 12"><path d="M3 9L9 3M4 3h5v5" stroke="#fff" stroke-width="1.6" fill="none"/></svg></span></div>
</header>
<div class="hero">
  <h1 class="abs display"><span class="boxed">Delivering</span> Strength<br>In Every Mile</h1>
</div>
<p class="abs hero-copy">We deliver a comprehensive range of open-deck and specialized transportation services—including flatbed, step deck, heavy haul, and over-dimensional freight solutions.</p>
<div class="btn" style="left:102px;top:461px;width:182px">Request a Quote <span class="arrow"><svg width="12" height="12" viewBox="0 0 12 12"><path d="M3 9L9 3M4 3h5v5" stroke="#fff" stroke-width="1.6" fill="none"/></svg></span></div>
<div class="btn" style="left:294px;top:461px;width:160px;padding-left:8px"><span class="arrow" style="margin:0;background:var(--ink)"><svg width="13" height="13" viewBox="0 0 24 24"><path d="M6.6 10.8a15 15 0 006.6 6.6l2.2-2.2c.3-.3.7-.4 1-.2 1.1.4 2.3.6 3.6.6.6 0 1 .4 1 1V20c0 .6-.4 1-1 1A17 17 0 013 4c0-.6.4-1 1-1h3.5c.6 0 1 .4 1 1 0 1.3.2 2.5.6 3.6.1.3 0 .7-.2 1z" fill="#fff"/></svg></span>Call Us Now</div>

<!-- STATS -->
<div class="abs stat" style="left:165px"><b>250</b><small>Lorem ipsum dolor sit</small></div>
<div class="abs stat-div" style="left:376px"></div>
<div class="abs stat" style="left:391px"><b>30K+</b><small>Lorem ipsum dolor sit</small></div>
<div class="abs stat-div" style="left:600px"></div>
<div class="abs stat" style="left:617px"><b>260</b><small>Lorem ipsum dolor sit</small></div>
<div class="abs stat-div" style="left:828px"></div>
<div class="abs stat" style="left:852px"><b>180</b><small>Lorem ipsum dolor sit</small></div>

<!-- ABOUT -->
<div class="abs about-bg"></div>
<section class="about">
  <div class="ph about-photo" role="img" aria-label="Photo of a white box truck speeding along a road"></div>
  <div class="abs play"><svg width="66" height="66" viewBox="0 0 66 66"><circle cx="33" cy="33" r="19" fill="none" stroke="var(--orange)" stroke-width="3"/><path d="M29 25l11 8-11 8z" fill="var(--orange)"/></svg></div>
  <div class="abs eyebrow" style="left:640px;top:1012px">About Company</div>
  <h2 class="abs display">Keeping Your Supply<br>Chain Moving
    <svg width="84" height="44" viewBox="0 0 84 44" style="vertical-align:-4px;margin-left:6px"><rect x="2" y="8" width="48" height="24" fill="none" stroke="var(--orange)" stroke-width="3"/><path d="M50 16h16l10 10v6H50z" fill="none" stroke="var(--orange)" stroke-width="3"/><circle cx="16" cy="36" r="5" fill="var(--orange)"/><circle cx="66" cy="36" r="5" fill="var(--orange)"/></svg></h2>
  <p class="abs">We deliver a comprehensive range of open-deck and specialized transportation services—including flatbed, step deck, heavy haul, and over-dimensional freight solutions. Backed by years of experience, a trusted nationwide carrier network, and a strong safety-first culture, we provide reliable, adaptable logistics support built around the unique requirements of every load.</p>
  <div class="btn" style="left:632px;top:1364px;width:160px">Learn More <span class="arrow"><svg width="12" height="12" viewBox="0 0 12 12"><path d="M3 9L9 3M4 3h5v5" stroke="#fff" stroke-width="1.6" fill="none"/></svg></span></div>
</section>

<!-- SERVICES -->
<section class="abs services">
  <div class="abs sec-head" style="top:56px"><div class="eyebrow">What We Do</div><h2 class="display" style="font-size:54px;margin-top:18px">Our Services</h2></div>
  <article class="card" style="left:73px">
    <h3>Flatbed<br>Transportation</h3>
    <p>From routine shipments to oversized and heavy-haul loads, we handle freight requiring proper securement, regulatory knowledge, and consistent on-time execution.</p>
    <div class="img" role="img" aria-label="Photo of a flatbed truck on a road" style="background:linear-gradient(180deg,transparent,#6a6a6e 45%,#3b2a22)"></div>
  </article>
  <article class="card active" style="left:344px">
    <h3>Step Deck<br>Transportation</h3>
    <p>Our step deck trucking services support tall, heavy, and specialized freight that requires additional height clearance and flexible loading options.</p>
    <span class="mini-btn">Learn More <i></i></span>
    <div class="img" role="img" aria-label="Photo of a red step deck trailer" style="height:120px;background:linear-gradient(180deg,transparent,#c54a2a 40%,#8a2a18)"></div>
  </article>
  <article class="card" style="left:610px">
    <h3>Step Deck<br>Transportation</h3>
    <p>From consumer goods to industrial materials, our dry van services provide the space, security, and consistency you need coast to coast.</p>
    <div class="img" role="img" aria-label="Photo of a truck on a highway at night" style="background:linear-gradient(180deg,transparent,#51604a 45%,#2a2a22)"></div>
  </article>
  <article class="card" style="left:877px">
    <h3>Heavy Haul<br>Transportation</h3>
    <p>We provide heavy haul trucking solutions for oversized, overweight, and over-dimensional freight.</p>
    <div class="img" role="img" aria-label="Photo of a red heavy haul truck carrying an oversize load" style="background:linear-gradient(180deg,transparent,#c8b98a 40%,#8a3a30)"></div>
  </article>
</section>
<div class="abs" style="left:595px;top:2067px;width:1px;height:68px;background:var(--line)"></div>

<!-- WHY CHOOSE US -->
<section class="abs why">
  <div class="abs sec-head" style="top:64px"><div class="eyebrow">Why We Are</div><h2 class="display" style="font-size:54px;margin-top:18px">Why Choose Us</h2></div>
  <svg class="abs" style="left:0;top:0" width="1200" height="674" viewBox="0 0 1200 674">
    <g fill="none" stroke="var(--orange)" stroke-width="2.5">
      <path d="M155 290v64q0 12 12 12h255"/>
      <path d="M155 544v-64q0-12 12-12h255"/>
      <path d="M1052 290v64q0 12-12 12H785"/>
      <path d="M1052 544v-64q0-12-12-12H785"/>
    </g>
    <g fill="var(--brown)" stroke="var(--orange)" stroke-width="2"><circle cx="155" cy="290" r="6"/><circle cx="155" cy="544" r="6"/><circle cx="1052" cy="290" r="6"/><circle cx="1052" cy="544" r="6"/></g>
  </svg>
  <div class="icon-ring" style="left:108px;top:185px"><svg width="46" height="46" viewBox="0 0 46 46" fill="none" stroke="#fff" stroke-width="2.5"><circle cx="20" cy="22" r="14"/><path d="M20 14v8l5 3"/><circle cx="33" cy="33" r="7" fill="#fff"/><path d="M30 33l2 2 4-4" stroke="var(--brown)"/></svg></div>
  <div class="abs feat" style="left:220px;top:196px;width:240px"><h4>Reliable &amp;<br>On-Time Delivery</h4><p>We ensure every shipment reaches its destination safely and on schedule.</p></div>
  <div class="icon-ring" style="left:1005px;top:185px"><svg width="46" height="46" viewBox="0 0 46 46" fill="none" stroke="#fff" stroke-width="2.5"><circle cx="23" cy="14" r="5"/><circle cx="11" cy="20" r="4"/><circle cx="35" cy="20" r="4"/><path d="M14 36v-6a9 9 0 0118 0v6zM4 36v-4a7 7 0 0110-6M42 36v-4a7 7 0 00-10-6"/></svg></div>
  <div class="abs feat" style="left:740px;top:196px;width:252px;text-align:right"><h4>Experienced &amp;<br>Professional Team</h4><p>Our logistics experts bring years of industry experience to every shipment.</p></div>
  <div class="icon-ring" style="left:108px;top:480px"><svg width="46" height="46" viewBox="0 0 46 46" fill="none" stroke="#fff" stroke-width="2.5"><path d="M14 6a8 8 0 018 8c0 6-8 14-8 14S6 20 6 14a8 8 0 018-8z"/><circle cx="14" cy="14" r="3"/><path d="M14 32c0 6 18 0 18 6"/><circle cx="36" cy="38" r="3"/></svg></div>
  <div class="abs feat" style="left:220px;top:458px;width:260px"><h4>Global Network<br>&amp; Reach</h4><p>With a strong worldwide logistics network, we connect businesses across borders.</p></div>
  <div class="icon-ring" style="left:1005px;top:480px"><svg width="50" height="40" viewBox="0 0 50 40" fill="none" stroke="#fff" stroke-width="2.5"><path d="M6 8h24v20H6zM30 14h8l6 7v7H30"/><circle cx="14" cy="31" r="4"/><circle cx="36" cy="31" r="4"/><path d="M0 16h10M2 22h8"/></svg></div>
  <div class="abs feat" style="left:740px;top:468px;width:252px;text-align:right"><h4>Customized<br>Logistics Solutions</h4><p>We tailor our services to match your unique shipping and business needs.</p></div>
  <div class="abs center-badge">TQ Freight<br>Global</div>
</section>

<!-- INDUSTRIES -->
<section class="abs industries">
  <div class="abs sec-head" style="top:74px"><div class="eyebrow">Who We Serve</div><h2 class="display" style="font-size:54px;margin-top:18px">Industries &nbsp;We Serve</h2></div>
  <div class="ind" style="left:93px"><div class="tile"><svg width="30" height="30" viewBox="0 0 30 30" fill="#fff"><path d="M4 14h22l-2 12H6z"/><circle cx="10" cy="9" r="4"/><circle cx="19" cy="8" r="5"/></svg></div>Food &amp; Beverage</div>
  <div class="ind active" style="left:303px"><div class="tile"><svg width="30" height="30" viewBox="0 0 30 30" fill="none" stroke="#fff" stroke-width="2.2"><path d="M3 5h4l3 14h14l3-10H9"/><circle cx="12" cy="24" r="2"/><circle cx="22" cy="24" r="2"/></svg></div>E-Commerce &amp; Retail
    <div style="position:absolute;left:28px;bottom:-14px;width:28px;height:28px;border-radius:50%;background:var(--orange)"></div></div>
  <div class="ind" style="left:516px"><div class="tile"><svg width="30" height="30" viewBox="0 0 30 30" fill="#fff"><circle cx="15" cy="9" r="5"/><rect x="3" y="18" width="7" height="8"/><rect x="11.5" y="18" width="7" height="8"/><rect x="20" y="18" width="7" height="8"/></svg></div>Manufacturing</div>
  <div class="ind" style="left:726px"><div class="tile"><svg width="30" height="30" viewBox="0 0 30 30" fill="none" stroke="#fff" stroke-width="2.2"><rect x="7" y="4" width="16" height="22" rx="2"/><path d="M15 10v8M11 14h8"/></svg></div>Pharma &amp; Healthcare</div>
  <div class="ind" style="left:937px"><div class="tile"><svg width="30" height="30" viewBox="0 0 30 30" fill="#fff"><path d="M15 3l12 7H3z"/><rect x="6" y="12" width="3" height="11"/><rect x="13.5" y="12" width="3" height="11"/><rect x="21" y="12" width="3" height="11"/><rect x="3" y="24" width="24" height="3"/></svg></div>Government</div>
</section>

<!-- TESTIMONIALS -->
<section class="testi">
  <div class="abs eyebrow" style="left:116px;top:3420px">Testimonials</div>
  <h2 class="abs display">See What<br>Our Customer</h2>
  <p class="abs" style="left:114px;top:3648px;width:300px;font-size:11.5px;line-height:1.6;color:var(--muted)">Lorem ipsum dolor sit amet, consectetur adipiscing elit, sed do eiusmod tempor incididunt</p>
  <div class="circ-btn" style="left:122px"><svg width="12" height="12" viewBox="0 0 12 12"><path d="M10 6H2M5 3L2 6l3 3" stroke="#fff" stroke-width="1.6" fill="none"/></svg></div>
  <div class="circ-btn" style="left:172px"><svg width="12" height="12" viewBox="0 0 12 12"><path d="M2 6h8M7 3l3 3-3 3" stroke="#fff" stroke-width="1.6" fill="none"/></svg></div>
  <article class="quote" style="left:458px"><div class="qm">❝</div><p>"Lorem ipsum dolor sit amet, consectetur adipiscing elit, sed do eiusmod tempor incididunt ut labore et dolore magna aliqua. Quis ipsum suspendisse ultrices gravida. Risus commodo viverra maecenas accumsan lacus vel facilisis"</p>
    <div class="who"><div class="av"></div><div><b>Mara Velden</b><div class="stars">★★★★★</div></div></div></article>
  <article class="quote" style="left:806px"><div class="qm">❝</div><p>"Lorem ipsum dolor sit amet, consectetur adipiscing elit, sed do eiusmod tempor incididunt ut labore et dolore magna aliqua. Quis ipsum suspendisse ultrices gravida. Risus commodo viverra maecenas accumsan lacus vel facilisis"</p>
    <div class="who"><div class="av"></div><div><b>Mara Velden</b><div class="stars">★★★★★</div></div></div></article>
</section>

<!-- CONTACT -->
<section class="abs contact">
  <div class="abs" style="left:92px;top:76px;width:490px;height:490px;border-radius:50%;border:4px solid var(--orange)"></div>
  <div class="ph" role="img" aria-label="Photo of a fleet of semi-trucks parked in a row" style="left:100px;top:84px;width:474px;height:474px;border-radius:50%;background:radial-gradient(circle at 40% 50%,#d8c6c0 0%,#9a7e76 40%,#4a2a22 100%)"></div>
  <div class="abs eyebrow" style="left:622px;top:112px">Contact Us</div>
  <h2 class="abs display" style="left:618px;top:140px;font-size:56px">Request a &nbsp;Quote</h2>
  <div class="field" style="left:618px;top:219px;width:228px">👤 First Name</div>
  <div class="field" style="left:856px;top:219px;width:230px">👤 Last Name</div>
  <div class="field" style="left:618px;top:280px;width:228px">✉ Email address</div>
  <div class="field" style="left:856px;top:280px;width:230px">☎ Phone</div>
  <div class="field" style="left:618px;top:342px;width:468px;height:107px;align-items:flex-start;padding-top:16px">💬 Message</div>
  <div class="btn" style="left:614px;top:475px;width:170px">Send Message <span class="arrow"><svg width="12" height="12" viewBox="0 0 12 12"><path d="M3 9L9 3M4 3h5v5" stroke="#fff" stroke-width="1.6" fill="none"/></svg></span></div>
</section>

<!-- FOOTER -->
<footer class="abs footer"></footer>
<div class="abs" style="left:116px;top:4570px;width:154px;height:154px;border-radius:50%;border:3px solid var(--orange);background:var(--brown);display:flex;align-items:center;justify-content:center;text-align:center;font-family:'Bebas Neue',sans-serif;font-size:24px;line-height:1">TQ Freight<br>Global</div>
<div class="abs" style="left:138px;top:4727px;width:34px;height:34px;border-radius:50%;background:var(--orange)" role="img" aria-label="Social profile"></div>
<div class="abs" style="left:186px;top:4727px;width:34px;height:34px;border-radius:50%;background:var(--orange)" role="img" aria-label="Social profile"></div>
<div class="abs" style="left:234px;top:4727px;width:34px;height:34px;border-radius:50%;background:var(--orange)" role="img" aria-label="Social profile"></div>
<div class="abs" style="left:588px;top:4570px;width:1px;height:200px;background:#3d2218"></div>
<div class="abs" style="left:818px;top:4570px;width:1px;height:200px;background:#3d2218"></div>
<div class="foot-link" style="top:4565px"><span style="color:var(--orange);font-size:16px">⌂</span>Home</div>
<div class="foot-link" style="top:4617px"><span style="color:var(--orange);font-size:16px">☺</span>About</div>
<div class="foot-link" style="top:4669px"><span style="color:var(--orange);font-size:16px">▦</span>Industries</div>
<div class="foot-link" style="top:4721px;border:0"><span style="color:var(--orange);font-size:16px">☎</span>Contact Us</div>
<div class="abs foot-col" style="left:643px;top:4566px"><h5>Services</h5><ul><li>Flatbed</li><li>Step Deck</li><li>Dry Van</li><li>Heavy Haul</li></ul></div>
<div class="abs foot-col" style="left:871px;top:4566px"><h5>Newsletter Sign Up</h5></div>
<div class="field" style="left:871px;top:4614px;width:236px;height:34px;font-size:11px;padding-left:14px">✉ Email address</div>
<div class="btn" style="left:871px;top:4662px;width:236px;height:36px;font-size:13px;padding-left:76px">Subscribe Now <span class="arrow" style="width:24px;height:24px"><svg width="10" height="10" viewBox="0 0 12 12"><path d="M3 9L9 3M4 3h5v5" stroke="#fff" stroke-width="1.6" fill="none"/></svg></span></div>
<div class="abs big-word">TQ Freight Global</div>
<p class="abs" style="left:0;top:4926px;width:1200px;text-align:center;font-size:12px;color:#a58b80">© 2026. An independent agent of Halvern Carriers LLC.</p>
<div class="abs" style="left:1070px;top:4922px;width:22px;height:22px;border-radius:50%;background:var(--orange)"></div>

</body>
</html>
```